Meadowlark Property Review is a leading provider of residential appraisal and home inspection products in S

I need a business card/logo designed that obviously describes my business. We are a residential appraisal and home inspection company in Springfield, MO. We offer residential appraisals, home inspection, pest inspection and radon gas measurement. We have been in business for 18 years and hold state certified residential appraisal licenses and OBREX certified home inspection licenses. I have a logo that I really like and will attach, but would be open to new suggestions. I like more modern designs than traditional and would like a two sided card with our services, licenses and qualifications on the back.

```html
<!DOCTYPE html>
<html lang="en">
<head>
<meta charset="utf-8">
<title>Meadowlark Property Review – Business Card</title>
<link href="https://fonts.googleapis.com/css2?family=Open+Sans:wght@400;600;700;800&display=swap" rel="stylesheet">
<style>
  :root {
    --bg: #ece8e2;
    --card: #ffffff;
    --brown: #6e5638;
    --orange: #f28a1e;
    --orange-soft: #f6b04a;
    --gold: #d6a92c;
    --ink: #2b2b2b;
    --ink-soft: #444;
  }
  * { box-sizing: border-box; margin: 0; padding: 0; }
  html, body { width: 1200px; height: 913px; overflow: hidden; }
  body {
    background: var(--bg);
    font-family: "Open Sans", Arial, sans-serif;
    position: relative;
  }
  .card {
    position: absolute;
    top: 301px;
    width: 540px;
    height: 310px;
    background: var(--card);
    border-radius: 16px;
    overflow: hidden;
    box-shadow: 0 6px 20px rgba(0,0,0,.18);
  }
  .card--front { left: 40px; }
  .card--back { left: 620px; }
  .card__art { position: absolute; inset: 0; width: 100%; height: 100%; }

  /* Front */
  .address {
    position: absolute; left: 26px; top: 28px;
    font-weight: 700; font-size: 14px; line-height: 1.35; color: var(--ink);
    width: 230px;
  }
  .badge {
    position: absolute; left: 26px; top: 152px;
    width: 30px; height: 30px; border-radius: 50%;
    background: var(--gold);
  }
  .wordmark {
    position: absolute;
    font-weight: 800; color: var(--brown); line-height: 1.05;
  }
  .card--front .wordmark { left: 66px; top: 148px; font-size: 17px; width: 150px; }
  .contact {
    position: absolute; right: 24px; top: 30px;
    text-align: right; color: #fff;
  }
  .contact__name { font-size: 22px; font-weight: 700; letter-spacing: .5px; }
  .contact__role { font-size: 12px; font-weight: 700; color: var(--orange); letter-spacing: 1px; margin-bottom: 12px; }
  .contact__line { font-size: 13.5px; line-height: 1.55; display: flex; justify-content: flex-end; align-items: center; gap: 6px; }
  .contact__line svg { width: 11px; height: 11px; flex: none; }

  /* Back */
  .intro {
    position: absolute; right: 22px; top: 22px; width: 330px;
    font-size: 9px; font-weight: 600; line-height: 1.35; color: var(--ink-soft);
  }
  .card--back .wordmark { left: 34px; top: 128px; font-size: 26px; width: 220px; }
  .services {
    position: absolute; right: 22px; top: 104px;
    list-style: none; text-align: right;
  }
  .services li {
    font-size: 14px; line-height: 1.4; color: var(--ink); text-transform: uppercase;
    display: flex; justify-content: flex-end; align-items: center; gap: 8px;
  }
  .services li::after {
    content: ""; width: 8px; height: 8px; border-radius: 50%; background: var(--orange-soft);
  }
</style>
</head>
<body>

<section class="card card--front">
  <svg class="card__art" viewBox="0 0 540 310" preserveAspectRatio="none" aria-hidden="true">
    <defs>
      <linearGradient id="taupe" x1="0" y1="0" x2="1" y2="1">
        <stop offset="0" stop-color="#c9b497"/>
        <stop offset="1" stop-color="#8a7256"/>
      </linearGradient>
    </defs>
    <path d="M300 0 L540 0 L540 310 L30 310 C170 300 270 200 300 0 Z" fill="url(#taupe)"/>
    <path d="M292 0 C262 200 170 298 0 302" fill="none" stroke="var(--orange)" stroke-width="6"/>
    <path d="M284 0 C252 190 160 290 0 292" fill="none" stroke="var(--orange-soft)" stroke-width="1.5"/>
  </svg>

  <p class="address">Meadowlark Property Review 4820 S Larkspur Avenue Suite C Springfield, MO 65804</p>
  <span class="badge"></span>
  <p class="wordmark">Meadowlark Property Review</p>

  <div class="contact">
    <p class="contact__name">DANA WHITLOCK</p>
    <p class="contact__role">OWNER</p>
    <p class="contact__line">417-555-0142
      <svg viewBox="0 0 12 12"><path d="M2 1 L4.5 1 L5.5 3.5 L4 4.8 C4.8 6.5 5.5 7.2 7.2 8 L8.5 6.5 L11 7.5 L11 10 C6 10.5 1.5 6 2 1 Z" fill="var(--orange)"/></svg>
    </p>
    <p class="contact__line">417-555-0187
      <svg viewBox="0 0 12 12"><rect x="1" y="2" width="10" height="8" rx="1" fill="none" stroke="var(--orange)" stroke-width="1.3"/><rect x="3" y="4" width="6" height="2" fill="var(--orange)"/></svg>
    </p>
    <p class="contact__line">info@meadowlarkreview.com
      <svg viewBox="0 0 12 12"><rect x="1" y="2.5" width="10" height="7" fill="none" stroke="var(--orange)" stroke-width="1.3"/><path d="M1 2.5 L6 6.5 L11 2.5" fill="none" stroke="var(--orange)" stroke-width="1.3"/></svg>
    </p>
    <p class="contact__line">www.meadowlarkreview.com
      <svg viewBox="0 0 12 12"><circle cx="6" cy="6" r="5" fill="none" stroke="var(--orange)" stroke-width="1.3"/><path d="M1 6 H11 M6 1 C3 4 3 8 6 11 C9 8 9 4 6 1" fill="none" stroke="var(--orange)" stroke-width="1"/></svg>
    </p>
  </div>
</section>

<section class="card card--back">
  <p class="intro">With years of experience behind us, we're prepared to tackle anything from a first Time buyer's starter home or a seasoned buyer purchasing a luxurious dream home</p>
  <p class="wordmark">Meadowlark Property Review</p>
  <ul class="services">
    <li>Appraisal</li>
    <li>Home Inspection</li>
    <li>Termite</li>
    <li>Radon</li>
    <li>Well &amp; Septic Inspection</li>
    <li>Energy Audits</li>
  </ul>
</section>

</body>
</html>
```